Tech business card design

We need an amazing business card design for our new business 'Pexla' a marketing tech startup based in Sydney, Australia. We provide an online marketplace for businesses to search and buy advertising media, connect with service providers and learn more about marketing. We wish to communicate 'cool tech', reliability and professionalism and design based around our logo.

Target Market(s)

Business Owners

Contact Information for Business Card

Name
Position
Email Address
Website
Phone Number

Font styles to use
Other font styles liked:
• Avenir & Avenir Next

Colors

Designer to choose colors to be used in the design.

```html
<!DOCTYPE html>
<html lang="en">
<head>
<meta charset="utf-8">
<title>Pexla Business Card</title>
<link href="https://fonts.googleapis.com/css2?family=Nunito+Sans:wght@400;700;800&display=swap" rel="stylesheet">
<style>
  :root {
    --backdrop: #e2dfe0;
    --stock: #c9c8c8;
    --white: #ffffff;
    --navy: #1c1e42;
    --ink: #3c3c3c;
  }
  * { margin: 0; padding: 0; box-sizing: border-box; }
  html, body {
    width: 1200px; height: 1044px; overflow: hidden;
    background: var(--backdrop);
    font-family: "Nunito Sans", sans-serif;
  }
  .card {
    position: absolute; top: 73px;
    width: 517px; height: 905px;
    background: var(--stock);
  }
  .card--front { left: 48px; }
  .card--back { left: 625px; }

  .logo-panel {
    position: absolute; left: 53px; width: 412px;
    background: var(--white);
  }
  .card--front .logo-panel { top: 84px; height: 296px; }
  .card--back .logo-panel { top: 130px; height: 465px; }

  .wordmark {
    position: absolute;
    font-weight: 800; color: var(--navy);
    font-size: 112px; line-height: 1; letter-spacing: -2px;
  }
  .card--front .wordmark { left: 40px; top: 92px; }
  .card--back .wordmark {
    left: 191px; top: 232px;
    transform: translate(-50%, -50%) rotate(-90deg);
    white-space: nowrap;
  }

  .name-band {
    position: absolute; left: 53px; top: 380px;
    width: 412px; height: 103px;
    background: var(--navy); color: var(--white);
    padding: 22px 0 0 42px;
  }
  .name-band .name { font-weight: 700; font-size: 22px; line-height: 1.3; }
  .name-band .role { font-weight: 400; font-size: 26px; line-height: 1.3; }

  .contact {
    position: absolute; left: 95px;
    color: var(--ink); font-size: 22px; line-height: 1;
    display: flex; align-items: center; gap: 10px;
  }
  .contact svg { width: 22px; height: 22px; flex: none; }
  .contact--phone { top: 520px; }
  .contact--email { top: 558px; }
  .contact--web { top: 792px; letter-spacing: 2.5px; }

  .address {
    position: absolute; left: 95px; top: 634px;
    color: var(--ink); font-size: 22px; line-height: 30px;
  }
  .divider {
    position: absolute; left: 95px; top: 754px;
    width: 124px; height: 3px; background: var(--navy);
  }

  .url-band {
    position: absolute; left: 53px; top: 595px;
    width: 412px; height: 165px;
    background: var(--navy); color: var(--white);
    display: flex; align-items: center; justify-content: center;
    font-size: 29px; letter-spacing: 3px;
  }
</style>
</head>
<body>
  <section class="card card--front">
    <div class="logo-panel">
      <span class="wordmark">Pexla</span>
    </div>
    <div class="name-band">
      <p class="name">ALEX REED</p>
      <p class="role">Position</p>
    </div>
    <p class="contact contact--phone">
      <svg viewBox="0 0 24 24" aria-hidden="true"><circle cx="12" cy="12" r="10.5" fill="none" stroke="#3c3c3c" stroke-width="1.5"/><path d="M9 6.5l2 2.5-1.2 1.3c.8 1.8 2 3 3.8 3.8l1.3-1.2 2.5 2-1.2 2c-4.5-.5-8.3-4.3-8.8-8.8z" fill="#3c3c3c"/></svg>
      012-345-6789
    </p>
    <p class="contact contact--email">
      <svg viewBox="0 0 24 24" aria-hidden="true"><rect x="1.5" y="5" width="21" height="14" fill="#3c3c3c"/><path d="M1.5 5l10.5 8 10.5-8M1.5 19l8-7M22.5 19l-8-7" fill="none" stroke="#c9c8c8" stroke-width="1.4"/></svg>
      info@pexla.com
    </p>
    <p class="address">Street name City Name,<br>Zipcode,012345</p>
    <div class="divider"></div>
    <p class="contact contact--web">
      <svg viewBox="0 0 24 24" aria-hidden="true"><g fill="none" stroke="#3c3c3c" stroke-width="1.4"><circle cx="12" cy="12" r="10.5"/><ellipse cx="12" cy="12" rx="4.5" ry="10.5"/><path d="M1.5 12h21M3.5 6.5h17M3.5 17.5h17M12 1.5v21"/></g></svg>
      www.pexla.com
    </p>
  </section>

  <section class="card card--back">
    <div class="logo-panel">
      <span class="wordmark">Pexla</span>
    </div>
    <div class="url-band">www.pexla.com</div>
  </section>
</body>
</html>
```